****Business Card Design for Quarrystone Development. Design based around attached logo/company name

I’m looking for business card design for my company Quarrystone Development Group,LLC. Design should be professional, sharp and minimal. Outside of the attached logos, greyscale colors for remainder of cards. My thoughts are two-sided card with attached logo on one side and my info on the other but open to one-sided as well with right design.
Target Market(s)
Real estate professionals including banks, private investors, property owners, developers, commercial tenants like Brewlantern, Grovika or Tanquist’s.
Industry/Entity Type
Commercial real estate development and investments.
Contact Information for Business Card
Name, title, email, phone #’s, web address and physical address
Font styles to use
Other font styles liked:
- Helvetica, Garamond, etc
Colors
Designer to choose only greyscale colors for use in the design.
Requirements
Must have
- Attached logo first or second options.
Nice to have
- Two sided card with logo on one side. Attached Logo/company name can be laid out any way that flows as long as it’s legible.name
Should not have
- No loud colors. ***Please do not include logo, I have removed the company design with a logo image.

```html
<!DOCTYPE html>
<html lang="en">
<head>
<meta charset="utf-8">
<title>Quarrystone Development Group, LLC — Business Cards</title>
<link rel="stylesheet" href="https://fonts.googleapis.com/css2?family=Cinzel:wght@400&family=Tinos&family=Roboto:wght@400&display=swap">
<style>
  :root {
    --backdrop: #2a2a2a;
    --card-light: #f5f5f5;
    --card-shade: #e4e4e5;
    --ink: #4b505d;
    --ink-soft: #5a5f6b;
    --band: #525866;
    --band-text: #f1f2f4;
    --rule: #5d6270;
  }
  * { box-sizing: border-box; margin: 0; padding: 0; }
  html, body {
    width: 1200px; height: 1138px; overflow: hidden;
    background: var(--backdrop);
  }
  .card {
    position: absolute;
    width: 620px; height: 375px;
    border-radius: 16px;
    overflow: hidden;
    background: linear-gradient(160deg, var(--card-light) 0%, var(--card-shade) 100%);
    color: var(--ink);
  }
  .card--front { left: 272px; top: 184px; }
  .card--back  { left: 274px; top: 606px; }

  .wordmark {
    font-family: "Cinzel", serif;
    font-weight: 400;
    color: var(--ink);
    line-height: 1;
  }
  .wordmark__name { display: block; font-size: 44px; letter-spacing: 1px; }
  .wordmark__sub  { display: block; font-size: 15px; letter-spacing: 3.2px; margin-top: 12px; }

  .card--front .wordmark {
    position: absolute; left: 0; right: 0; top: 142px; text-align: center;
  }
  .front-site {
    position: absolute; left: 0; right: 0; top: 334px;
    display: flex; align-items: center; justify-content: center; gap: 16px;
    font-family: "Roboto", sans-serif; font-size: 15px; color: var(--ink-soft);
  }
  .front-site__rule { width: 70px; height: 2px; background: var(--rule); border-radius: 1px; }

  .card--back .wordmark { position: absolute; left: 24px; top: 54px; }

  .person { position: absolute; left: 24px; top: 214px; font-family: "Tinos", serif; }
  .person__name { font-family: "Cinzel", serif; font-size: 23px; letter-spacing: 0.5px; }
  .person__title { font-size: 16px; margin-top: 4px; color: var(--ink-soft); }
  .person__address { font-size: 16px; line-height: 23px; margin-top: 26px; color: var(--ink-soft); }

  .contacts { position: absolute; left: 350px; top: 216px; list-style: none; font-family: "Tinos", serif; font-size: 16px; color: var(--ink-soft); }
  .contacts li { display: flex; align-items: center; height: 22px; }
  .contacts svg { width: 13px; height: 13px; margin-right: 14px; fill: var(--ink); }

  .footer-band { position: absolute; left: 0; bottom: 0; width: 620px; height: 46px; }
  .footer-band__text {
    position: absolute; right: 30px; bottom: 16px;
    font-family: "Tinos", serif; font-size: 16px; color: var(--band-text);
  }
</style>
</head>
<body>
  <section class="card card--front">
    <div class="wordmark">
      <span class="wordmark__name">QUARRYSTONE</span>
      <span class="wordmark__sub">DEVELOPMENT GROUP, LLC</span>
    </div>
    <div class="front-site">
      <span class="front-site__rule"></span>
      <span>www.quarrystonedev.com</span>
      <span class="front-site__rule"></span>
    </div>
  </section>

  <section class="card card--back">
    <div class="wordmark">
      <span class="wordmark__name">QUARRYSTONE</span>
      <span class="wordmark__sub">DEVELOPMENT GROUP, LLC</span>
    </div>

    <div class="person">
      <p class="person__name">DANIEL REEVE WALSH</p>
      <p class="person__title">Managing Director</p>
      <p class="person__address">410 Ledgerock Ave., Fairhollow,<br>Elm County, US 204318</p>
    </div>

    <ul class="contacts">
      <li><svg viewBox="0 0 16 16"><path d="M2 5c0-1 1-2 6-2s6 1 6 2v1h-3V5H5v1H2zM4 7h8l2 6H2z"/></svg>555-014-2290</li>
      <li><svg viewBox="0 0 16 16"><path d="M1 3h14v10H1zm1.5 1.2V5l5.5 4 5.5-4v-.8L8 8z"/></svg>daniel@quarrystonedev.com</li>
      <li><svg viewBox="0 0 16 16"><path d="M8 1a7 7 0 1 0 0 14A7 7 0 0 0 8 1zm-5.4 6h2.5a11 11 0 0 1 .5-3.5A5.6 5.6 0 0 0 2.6 7zm0 2a5.6 5.6 0 0 0 3 3.5A11 11 0 0 1 5.1 9zm4 0c.1 2 .7 3.7 1.4 4.4.7-.7 1.3-2.4 1.4-4.4zm2.8-2C9.3 5 8.7 3.3 8 2.6 7.3 3.3 6.7 5 6.6 7zm1.5 2a11 11 0 0 1-.5 3.5 5.6 5.6 0 0 0 3-3.5zm2.5-2a5.6 5.6 0 0 0-3-3.5 11 11 0 0 1 .5 3.5z"/></svg>www.quarrystonedev.com</li>
    </ul>

    <svg class="footer-band" viewBox="0 0 620 46" aria-hidden="true">
      <path d="M0 32H268L282 6Q285 0 292 0H620V46H0z" fill="var(--band)"/>
    </svg>
    <p class="footer-band__text">Quarrystone Development Group, LLC</p>
  </section>
</body>
</html>
```